Business Card Design Project

Business Card
We are rebranding with a new logo
Industry/Entity Type
Business
Contact Information for Business Card
Dennis Morvale +61 487215963 dennis@quorv.com.au P.O. Box 872 Fernlow QLD 4309
Requirements
Must have
- Logo

```html
<!DOCTYPE html>
<html lang="en">
<head>
<meta charset="utf-8">
<title>Quorv International – Business Card</title>
<link rel="stylesheet" href="https://fonts.googleapis.com/css2?family=Arimo:wght@400;700&display=swap">
<style>
  :root {
    --backdrop: #202428;
    --card: #ffffff;
    --brand-blue: #1592cf;
    --brand-blue-deep: #136a9f;
    --brand-blue-light: #22b0e6;
    --brand-orange: #f28a1f;
    --ink: #333a40;
    --ink-soft: #6b7379;
  }
  * { margin: 0; padding: 0; box-sizing: border-box; }
  html, body {
    width: 1200px;
    height: 902px;
    overflow: hidden;
    background: var(--backdrop);
    font-family: "Arimo", Arial, sans-serif;
  }
  .business-card {
    position: absolute;
    left: 150px;
    top: 193px;
    width: 900px;
    height: 515px;
    background: var(--card);
    border-radius: 24px;
    overflow: hidden;
    box-shadow: 0 18px 40px rgba(0,0,0,0.45);
  }
  .decor-panel {
    position: absolute;
    left: 0;
    top: 0;
    width: 320px;
    height: 515px;
    background: linear-gradient(160deg, var(--brand-blue-light) 0%, var(--brand-blue) 55%, var(--brand-orange) 100%);
  }
  .brand-name {
    position: absolute;
    right: 62px;
    top: 58px;
    font-size: 34px;
    font-weight: 700;
    color: var(--brand-blue);
    letter-spacing: 0.5px;
  }
  .person {
    position: absolute;
    right: 62px;
    top: 162px;
    text-align: right;
  }
  .person-name {
    font-size: 30px;
    font-weight: 700;
    color: var(--brand-blue);
  }
  .person-role {
    margin-top: 4px;
    font-size: 15px;
    color: var(--ink-soft);
  }
  .edge-tab {
    position: absolute;
    right: -8px;
    top: 150px;
    width: 22px;
    height: 44px;
    border-radius: 10px;
    background: var(--brand-blue);
  }
  .contact-list {
    position: absolute;
    left: 400px;
    top: 262px;
    list-style: none;
    color: var(--ink);
    font-size: 20px;
    line-height: 1.3;
  }
  .contact-item {
    display: flex;
    align-items: flex-start;
    gap: 14px;
    margin-bottom: 6px;
  }
  .contact-item.address { margin-bottom: 24px; }
  .contact-icon {
    width: 20px;
    height: 20px;
    flex: none;
    margin-top: 3px;
    fill: var(--brand-blue);
  }
</style>
</head>
<body>
  <article class="business-card">
    <div class="decor-panel" role="img" aria-label="Decorative blue and orange brand graphic"></div>

    <div class="brand-name">Quorv International</div>

    <div class="person">
      <div class="person-name">Dennis Morvale</div>
      <div class="person-role">Owner</div>
    </div>
    <div class="edge-tab"></div>

    <ul class="contact-list">
      <li class="contact-item address">
        <svg class="contact-icon" viewBox="0 0 20 20" aria-hidden="true"><path d="M10 2 L1 10 H4 V18 H8 V13 H12 V18 H16 V10 H19 Z"/></svg>
        <span>P.O. Box 872<br>Fernlow QLD 4309</span>
      </li>
      <li class="contact-item phone">
        <svg class="contact-icon" viewBox="0 0 20 20" aria-hidden="true"><path d="M6 1 H14 A2 2 0 0 1 16 3 V17 A2 2 0 0 1 14 19 H6 A2 2 0 0 1 4 17 V3 A2 2 0 0 1 6 1 Z M6 4 V15 H14 V4 Z M9 16 H11 V18 H9 Z"/></svg>
        <span>+61 487215963</span>
      </li>
      <li class="contact-item email">
        <svg class="contact-icon" viewBox="0 0 20 20" aria-hidden="true"><path d="M1 4 H19 L10 11 Z M1 6 L10 13 L19 6 V16 H1 Z"/></svg>
        <span>dennis@quorv.com.au</span>
      </li>
    </ul>
  </article>
</body>
</html>
```